Business Card Design Project

I need a business card design for my law office. I already have a logo.

I am an employment attorney who represents clients who have been wrongfully terminated or have been discriminated against by their employer.

I would like a unique, clean design using the colors in the logo or colors that complement the logo.

Target Market(s)

Clients, potential clients, other attorneys and others.

Industry/Entity Type

Attorney

Requirements
Must have
• I would like to use both sides of the card.

The information on the card must be easy to read.

Here is my information:

T. Dale Ostrovin
3857 E. Harbel Blvd., Suite 204
Fresno, California 93814
559-618-3074
559-782-4531 fax
dale@lawtdo-example.com
Nice to have
• QR Code? I would like to see designs incorporating a nice-looking QR code. Look at this example:

Notice the second QR code in the article - the color.

```html
<!DOCTYPE html>
<html lang="en">
<head>
<meta charset="utf-8">
<title>Ostrovin Law Office – Business Card</title>
<link rel="stylesheet" href="https://fonts.googleapis.com/css2?family=Open+Sans:wght@400;600;700&display=swap">
<style>
  :root {
    --page-bg: #eceef0;
    --card-bg: #ffffff;
    --band-top: #d3e9ee;
    --band-bottom: #e3f7fa;
    --ink-blue: #1d5b9e;
    --text-blue: #2a6cb4;
    --brand-blue: #1f7fc8;
    --accent-deep: #0a5fc4;
    --accent-mid: #3a93cc;
    --accent-light: #8fd0f2;
  }
  html, body {
    margin: 0;
    padding: 0;
    width: 1200px;
    height: 1200px;
    overflow: hidden;
    background: var(--page-bg);
    font-family: "Open Sans", Arial, sans-serif;
  }
  .canvas {
    position: relative;
    width: 1200px;
    height: 1200px;
  }
  .card {
    position: absolute;
    left: 180px;
    width: 840px;
    height: 480px;
    background: var(--card-bg);
    box-shadow: 0 6px 22px rgba(0, 0, 0, 0.12);
    overflow: hidden;
  }
  .card--front { top: 90px; }
  .card--back  { top: 630px; }

  .front-band {
    position: absolute;
    left: 0; top: 0;
    width: 100%;
    height: 200px;
    background: linear-gradient(180deg, var(--band-top), var(--band-bottom));
  }
  .accent-art {
    position: absolute;
    left: 44px;
    top: 124px;
    width: 340px;
    height: 320px;
    background: linear-gradient(135deg, var(--accent-deep) 0%, var(--accent-mid) 55%, var(--accent-light) 100%);
    opacity: 0.9;
  }
  .brand {
    position: absolute;
    display: flex;
    align-items: center;
    color: var(--brand-blue);
    font-weight: 600;
    white-space: nowrap;
  }
  .brand__mark {
    background: var(--brand-blue);
    flex: none;
  }
  .brand--small {
    right: 56px;
    top: 78px;
    font-size: 24px;
    gap: 14px;
  }
  .brand--small .brand__mark { width: 30px; height: 30px; }

  .contact {
    position: absolute;
    left: 480px;
    top: 230px;
    color: var(--text-blue);
    font-size: 18px;
    font-style: normal;
    font-weight: 600;
    line-height: 1.3;
  }
  .contact__name {
    margin: 0 0 16px;
    color: var(--ink-blue);
    font-size: 26px;
    font-weight: 700;
  }
  .contact__group { margin: 0 0 12px; }

  .brand--large {
    left: 50%;
    top: 50%;
    transform: translate(-50%, -50%);
    font-size: 50px;
    gap: 26px;
  }
  .brand--large .brand__mark { width: 60px; height: 60px; }
</style>
</head>
<body>
<main class="canvas">
  <section class="card card--front" aria-label="Business card front">
    <div class="front-band"></div>
    <div class="accent-art" role="img" aria-label="Decorative graphic of blue circles"></div>
    <div class="brand brand--small">
      <span class="brand__mark"></span>
      <span class="brand__name">Ostrovin Law Office</span>
    </div>
    <address class="contact">
      <p class="contact__name">T. Dale Ostrovin</p>
      <p class="contact__group">3857 E. Harbel Blvd., Suite 204<br>Fresno, California 93814</p>
      <p class="contact__group">559-618-3074<br>559-782-4531 fax</p>
      <p class="contact__group">dale@lawtdo-example.com</p>
    </address>
  </section>

  <section class="card card--back" aria-label="Business card back">
    <div class="brand brand--large">
      <span class="brand__mark"></span>
      <span class="brand__name">Ostrovin Law Office</span>
    </div>
  </section>
</main>
</body>
</html>
```